The Plate Compass

Cutting Through the Noise to What Actually Works.

Nutrition book

Target Market(s)

People looking to be or get healthy and eat right.

```html
<!DOCTYPE html>
<html lang="en">
<head>
<meta charset="UTF-8">
<title>The Plate Compass</title>
<link href="https://fonts.googleapis.com/css2?family=Archivo:ital,wght@0,400;0,500;0,800;1,400&display=swap" rel="stylesheet">
<style>
  :root {
    --bg: #1b1b19;
    --orange: #e99e2a;
    --white: #f8f8f6;
    --bar: #5f5e56;
    --muted: #6c6b63;
  }
  * { margin: 0; padding: 0; box-sizing: border-box; }
  html, body { width: 811px; height: 1200px; overflow: hidden; background: var(--bg); }
  .cover {
    position: relative; width: 811px; height: 1200px;
    background: var(--bg); font-family: "Archivo", sans-serif;
  }
  .eyebrow {
    position: absolute; top: 104px; left: 0; width: 100%;
    text-align: center; color: var(--orange); font-size: 21px; font-weight: 500; letter-spacing: 0.5px;
  }
  .title {
    position: absolute; top: 140px; left: 0; width: 100%;
    text-align: center; color: var(--white); font-weight: 800;
    font-size: 80px; line-height: 87px; letter-spacing: -1px;
  }
  .axis {
    position: absolute; left: 67px; top: 332px; width: 11px; height: 506px; background: var(--orange);
  }
  .bar {
    position: absolute; left: 95.5px; height: 68.5px; background: var(--bar);
  }
  .bar-marker {
    position: absolute; left: 21px; top: 17px; width: 34px; height: 34px;
    border-radius: 50%; background: var(--orange);
  }
  .bar-label {
    position: absolute; left: 76px; top: 50%; transform: translateY(-46%);
    font-size: 30px; font-weight: 400; letter-spacing: -0.3px; white-space: nowrap;
  }
  .end-mark {
    position: absolute; color: var(--orange); font-size: 23px; font-weight: 500; letter-spacing: -0.3px;
  }
  .rule { position: absolute; left: 259px; top: 935.5px; width: 293px; height: 2px; background: var(--orange); }
  .tagline {
    position: absolute; top: 956px; left: 0; width: 100%; text-align: center;
    color: var(--muted); font-style: italic; font-size: 22px; line-height: 26px;
  }
  .author {
    position: absolute; top: 1098px; left: 0; width: 100%; text-align: center;
    color: var(--muted); font-style: italic; font-size: 22px;
  }
</style>
</head>
<body>
<main class="cover">
  <p class="eyebrow">THE</p>
  <h1 class="title">PLATE<br>COMPASS</h1>

  <div class="axis"></div>

  <div class="bar" style="top:332px; width:649px;">
    <div class="bar-marker" role="img" aria-label="Calories icon"></div>
    <span class="bar-label" style="color:#bdb6a1;">CALORIES</span>
  </div>
  <div class="bar" style="top:419.5px; width:562px;">
    <div class="bar-marker" role="img" aria-label="Protein icon"></div>
    <span class="bar-label" style="color:#b9b39f;">PROTEIN</span>
  </div>
  <div class="bar" style="top:507px; width:476px;">
    <div class="bar-marker" role="img" aria-label="Food quality icon"></div>
    <span class="bar-label" style="color:#b5af9b;">FOOD QUALITY</span>
  </div>
  <div class="bar" style="top:594.5px; width:389px;">
    <div class="bar-marker" role="img" aria-label="Meal timing icon"></div>
    <span class="bar-label" style="color:#ada793;">MEAL TIMING</span>
  </div>
  <div class="bar" style="top:682px; width:303px;">
    <div class="bar-marker" role="img" aria-label="Supplements icon"></div>
    <span class="bar-label" style="color:#9d9885;">SUPPLEMENTS</span>
  </div>
  <div class="bar" style="top:769.5px; width:216px;">
    <div class="bar-marker" role="img" aria-label="Noise icon"></div>
    <span class="bar-label" style="color:#878272;">NOISE</span>
  </div>

  <span class="end-mark" style="left:705px; top:350px;">MOST</span>
  <span class="end-mark" style="left:285.5px; top:792px;">LEAST</span>

  <div class="rule"></div>
  <p class="tagline">Cutting Through the Noise<br>to What Actually Works</p>
  <p class="author">AUTHOR NAME</p>
</main>
</body>
</html>
```